Looking for business card/letterhead/email signature

Take existing logo and create full design suite of collateral

Contact Information for Business Card

Use mock details that can be edited by us

Font styles to use
Sans Serif

```html
<!DOCTYPE html>
<html lang="en">
<head>
<meta charset="utf-8">
<title>Harlow Media – Stationery Suite</title>
<link href="https://fonts.googleapis.com/css2?family=Questrial&family=Roboto:wght@400;500;700&family=Roboto+Condensed:wght@400;700&display=swap" rel="stylesheet">
<style>
  :root{
    --backdrop:#dcdcdc;
    --paper:#ffffff;
    --navy:#0a4a8f;
    --ink:#555b63;
    --ink-dark:#3a3f45;
    --rule:#9aa0a6;
    --shadow:0 2px 5px rgba(0,0,0,.18);
  }
  *{margin:0;padding:0;box-sizing:border-box}
  html,body{width:1200px;height:738px;overflow:hidden}
  body{background:var(--backdrop);position:relative;font-family:"Roboto",Arial,sans-serif;color:var(--ink)}
  .sheet{position:absolute;background:var(--paper);box-shadow:var(--shadow);overflow:hidden}
  .brand-name{position:absolute;font-family:"Roboto",Arial,sans-serif;font-weight:700;color:var(--navy);white-space:nowrap;transform:translate(-50%,-50%);letter-spacing:-.2px}
  .brand-name.on-navy{color:#fff}
  .corner-disc{position:absolute;left:0;top:0}
  .contact-block{position:absolute;text-align:right;color:#fff;font-size:6.4px;line-height:8px;font-family:"Roboto",Arial,sans-serif}
  .contact-block .strong{font-weight:700}
  .contact-block .gap{margin-top:4px}
  .icon{width:6px;height:6px;vertical-align:-1px;margin-left:3px;fill:currentColor}

  /* Letterhead */
  .letterhead{left:66px;top:107px;width:452px;height:583px}
  .letterhead .salutation{position:absolute;left:40px;top:176px;font-family:"Questrial",Arial,sans-serif;font-size:12px;color:var(--ink-dark)}
  .letterhead .body-copy{position:absolute;left:40px;top:207px;width:374px;font-family:"Questrial",Arial,sans-serif;font-size:6.5px;line-height:9.6px;color:var(--ink)}
  .letterhead .body-copy p{margin-bottom:9.6px}
  .letterhead .closing{position:absolute;left:40px;top:411px;font-family:"Questrial",Arial,sans-serif;font-size:6.5px;color:var(--ink)}
  .letterhead .signature{position:absolute;left:36px;top:437px;width:80px;height:28px;background:linear-gradient(90deg,#e4ebf4,#eef2f8);border-radius:3px}
  .letterhead .contact-block{right:22px;top:519px}

  /* Email signature */
  .email-signature{left:582px;top:107px;width:521px;height:79px}
  .email-signature .divider{position:absolute;top:18px;width:1px;height:44px;background:var(--rule)}
  .email-signature .person{position:absolute;left:150px;top:29px;width:102px;text-align:center;font-family:"Roboto Condensed",Arial,sans-serif;color:var(--navy)}
  .email-signature .person .name{font-size:11px;font-weight:700;line-height:12px}
  .email-signature .person .role{font-size:7.5px;color:var(--ink-dark);line-height:9px}
  .email-signature .address{position:absolute;left:266px;top:27px;font-size:7px;line-height:9.4px;color:var(--ink-dark)}
  .email-signature .channels{position:absolute;left:406px;top:22px;font-size:7px;line-height:9.6px;color:var(--ink-dark);list-style:none}
  .email-signature .channels .icon{margin:0 5px 0 0;fill:var(--navy)}

  /* Business cards */
  .card-front{left:578px;top:203px;width:251px;height:143px}
  .card-front .contact-block{right:15px;top:67px;font-size:6.2px;line-height:7.8px}
  .card-front .contact-block .name{font-family:"Roboto Condensed",Arial,sans-serif;font-weight:700;font-size:9.5px;line-height:10px}
  .card-front .contact-block .role{font-family:"Roboto Condensed",Arial,sans-serif;font-size:7px;margin-bottom:3px}
  .card-back{left:850px;top:203px;width:251px;height:143px;background:var(--navy)}

  /* Envelope */
  .envelope-back{left:576px;top:362px;width:530px;height:230px;background:var(--paper);box-shadow:var(--shadow);position:absolute}
  .envelope-flap{position:absolute;left:0;top:0}
  .envelope-front{left:549px;top:458px;width:530px;height:231px}
  .envelope-front .contact-block{right:11px;top:184px}
</style>
</head>
<body>

<svg width="0" height="0" style="position:absolute" aria-hidden="true">
  <symbol id="i-phone" viewBox="0 0 10 10"><path d="M2.2 0.6l1.6 1.9-0.9 1.2c0.6 1.3 1.6 2.3 2.9 2.9l1.2-0.9 1.9 1.6-0.8 1.8C5.2 9.3 0.7 4.8 0.4 1.4z"/></symbol>
  <symbol id="i-mobile" viewBox="0 0 10 10"><path d="M2.5 0h5v10h-5zM3.4 1v7h3.2V1z"/></symbol>
  <symbol id="i-mail" viewBox="0 0 10 10"><path d="M0 2h10v6H0zM1 3v0.3l4 2.5 4-2.5V3z"/></symbol>
  <symbol id="i-globe" viewBox="0 0 10 10"><path d="M5 0a5 5 0 1 0 0.01 0zM2 3h6v1H2zm0 3h6v1H2zM4.5 1h1v8h-1z"/></symbol>
</svg>

<!-- Letterhead -->
<section class="sheet letterhead">
  <div class="brand-name" style="left:228px;top:116px;font-size:14px">Harlow Media</div>
  <p class="salutation">Dear Mr. Carter,</p>
  <div class="body-copy">
    <p>Thank you for meeting with our team last week. We have reviewed your notes and prepared a full plan for the new campaign, covering print, web and social channels. Our designers will share first drafts by the end of the month, and we will arrange a call to walk through each piece together. Please let us know if any dates need to change.</p>
    <p>The budget attached follows the figures we discussed. It includes design, copywriting and two rounds of revisions for every item. Printing costs are listed on a separate sheet so you can compare quotes from local suppliers before we place the order.</p>
    <p>Once the drafts are approved, we will prepare final files for your team and set up templates for letters, cards and email signatures. Training on the templates is included, and our support desk will remain open for any questions during the first three months after launch.</p>
    <p>We look forward to working with you and are confident the new materials will give your brand a clear and consistent look across every channel.</p>
  </div>
  <p class="closing">Sincerely,</p>
  <div class="signature" role="img" aria-label="Handwritten signature of Owen Carter"></div>
  <svg class="corner-disc" width="452" height="583" aria-hidden="true"><circle cx="390" cy="533" r="76" fill="var(--navy)"/></svg>
  <div class="contact-block">
    <div class="strong">Harlow Media</div>
    <div>2140 Willow Court</div>
    <div>Juneau, Alaska 34590</div>
    <div class="gap">555 210 4837<svg class="icon"><use href="#i-phone"/></svg></div>
    <div>hello@harlowmedia.com<svg class="icon"><use href="#i-mail"/></svg></div>
    <div>www.harlowmedia.com<svg class="icon"><use href="#i-globe"/></svg></div>
  </div>
</section>

<!-- Email signature -->
<section class="sheet email-signature">
  <div class="brand-name" style="left:68px;top:41px;font-size:12px">Harlow Media</div>
  <span class="divider" style="left:140px"></span>
  <div class="person"><div class="name">OWEN CARTER</div><div class="role">CEO/FOUNDER</div></div>
  <span class="divider" style="left:248px"></span>
  <div class="address">Harlow Media<br>2140 Willow Court<br>Juneau, Alaska 34590</div>
  <span class="divider" style="left:375px"></span>
  <ul class="channels">
    <li><svg class="icon"><use href="#i-phone"/></svg>555 210 4837</li>
    <li><svg class="icon"><use href="#i-mobile"/></svg>555 310 7721</li>
    <li><svg class="icon"><use href="#i-mail"/></svg>owen@harlowmedia.com</li>
    <li><svg class="icon"><use href="#i-globe"/></svg>www.harlowmedia.com</li>
  </ul>
</section>

<!-- Business card front -->
<section class="sheet card-front">
  <div class="brand-name" style="left:64px;top:43px;font-size:16px">Harlow Media</div>
  <svg class="corner-disc" width="251" height="143" aria-hidden="true"><circle cx="218" cy="117" r="84" fill="var(--navy)"/></svg>
  <div class="contact-block">
    <div class="name">Owen Carter</div>
    <div class="role">CEO/Founder</div>
    <div class="strong">Harlow Media</div>
    <div>2140 Willow Court</div>
    <div>Juneau, Alaska 34590</div>
    <div class="gap">555 210 4837<svg class="icon"><use href="#i-phone"/></svg></div>
    <div>owen@harlowmedia.com<svg class="icon"><use href="#i-mail"/></svg></div>
    <div>www.harlowmedia.com<svg class="icon"><use href="#i-globe"/></svg></div>
  </div>
</section>

<!-- Business card back -->
<section class="sheet card-back">
  <div class="brand-name on-navy" style="left:125px;top:73px;font-size:16px">Harlow Media</div>
</section>

<!-- Envelope back with flap -->
<section class="envelope-back">
  <svg class="envelope-flap" width="530" height="80" aria-hidden="true">
    <path d="M0 0H530L520 66Q518 76 506 76H26Q14 76 12 66Z" fill="var(--navy)"/>
  </svg>
  <div class="brand-name on-navy" style="left:252px;top:40px;font-size:11px">Harlow Media</div>
</section>

<!-- Envelope front -->
<section class="sheet envelope-front">
  <div class="brand-name" style="left:72px;top:46px;font-size:13px">Harlow Media</div>
  <svg class="corner-disc" width="530" height="231" aria-hidden="true"><circle cx="483" cy="182" r="68" fill="var(--navy)"/></svg>
  <div class="contact-block">
    <div class="strong">Harlow Media</div>
    <div>2140 Willow Court</div>
    <div>Juneau, Alaska 34590</div>
  </div>
</section>

</body>
</html>
```